Velmora Publishing

I made a website myself www.velmorapublishing.co.uk a few years ago but I need a new design, which I will code. One that I can be proud of, that 's sexy, to win new customers and showcase my publishing skills. This is a publishing website so I want the home page and books page to be fantastic. I have a logo already so will like the same colour scheme or thereabouts. I have current files and features that I would like to add to your creativity and experience.

Target Market(s)

Web Designers, Graphic Designers

Industry/Entity Type

Book Publisher

Number of Pages Required

5+ page

Font styles to use
Sans Serif

Colors
0255a3
ffffff
ec1f27

Requirements
Must have
• Menu and Sub Menu
• Footer
• Buy Page - Shopping Cart
• Upload feature on the submissions page
• video section on home page (how we publish books)
• Ad space section
Nice to have
• social media bar
• Zoom in page

```html
<!DOCTYPE html>
<html lang="en">
<head>
<meta charset="utf-8">
<title>Velmora Publishing – Home</title>
<link rel="stylesheet" href="https://fonts.googleapis.com/css2?family=Rajdhani:wght@500;600;700&family=Roboto:ital,wght@0,300;0,400;0,500;0,700;1,400&display=swap">
<style>
:root{
  --navy:#1c1f4d;
  --blue:#0255a3;
  --blue-deep:#0a3f7c;
  --red:#ec1f27;
  --green:#6dbf6f;
  --white:#ffffff;
  --ink:#222428;
  --text:#55585e;
  --muted:#8a8d92;
  --grey-band:#e6e6e6;
  --grey-box:#ececec;
  --numeral:#e3e3e3;
}
*{box-sizing:border-box;margin:0;padding:0}
html,body{width:1200px;height:3896px;overflow:hidden}
body{position:relative;background:var(--white);font-family:"Roboto",Arial,sans-serif;color:var(--text)}
.head{font-family:"Rajdhani","Roboto",sans-serif;font-weight:700}
section,header,footer{position:absolute;left:0;width:1200px}

/* hero */
.hero{top:0;height:662px;overflow:hidden}
.hero-photo{position:absolute;inset:0;background:linear-gradient(100deg,#f1efec 0%,#e4e1dc 35%,#c9c3bb 60%,#8d8279 80%,#d8d5d1 100%)}
.topbar{position:absolute;top:0;left:0;width:1200px;height:86px;background:var(--navy)}
.brand{position:absolute;left:72px;top:2px;width:106px;height:106px;border-radius:50%;background:var(--white);display:flex;align-items:center;justify-content:center;text-align:center;font-family:"Roboto",sans-serif;font-weight:700;font-size:14px;line-height:1.15;color:var(--navy);box-shadow:0 2px 6px rgba(0,0,0,.25)}
.menu{position:absolute;top:0;left:234px;height:86px;display:flex;align-items:center;list-style:none}
.menu li{font-family:"Roboto",sans-serif;font-weight:700;font-size:14px;color:var(--white);margin-right:38px;letter-spacing:.2px}
.menu-tools{position:absolute;top:31px;left:1052px;display:flex;gap:28px}
.hero-title{position:absolute;left:345px;top:291px;width:512px;text-align:center}
.hero-title h1{font-size:46px;line-height:46px;color:var(--white);letter-spacing:1px}
.hero-title p{font-size:34px;line-height:38px;color:var(--white);letter-spacing:.5px;padding-bottom:8px;border-bottom:3px solid var(--white)}
.btn-red{position:absolute;left:512px;top:446px;width:178px;height:42px;background:var(--red);color:var(--white);font-family:"Roboto",sans-serif;font-weight:700;font-size:16px;display:flex;align-items:center;justify-content:center}
.dots{position:absolute;top:614px;left:548px;display:flex;gap:5px}
.dots span{width:16px;height:16px;border-radius:50%;border:2px solid var(--blue);background:var(--white)}
.dots span.on{background:var(--blue)}

/* intro */
.intro{top:662px;height:273px;text-align:center}
.intro h2{position:absolute;top:58px;width:100%;font-family:"Roboto",sans-serif;font-weight:500;font-size:34px;color:var(--ink)}
.intro .rule{position:absolute;top:116px;left:524px;width:152px;height:2px;background:var(--blue)}
.intro p{position:absolute;top:146px;left:170px;width:860px;font-weight:300;font-size:24px;line-height:34px;color:var(--muted)}

/* category tiles */
.categories{top:935px;height:434px;background:var(--grey-band)}
.tile{position:absolute;top:125px;width:315px;height:246px;color:var(--white)}
.tile::after{content:"";position:absolute;inset:14px;border:2px solid rgba(255,255,255,.55)}
.tile-books{left:109px;background:var(--green)}
.tile-authors{left:442px;background:var(--blue)}
.tile-submissions{left:775px;background:var(--red)}
.tile svg{position:absolute;left:50%;top:56px;transform:translateX(-50%)}
.tile span{position:absolute;left:0;right:0;top:158px;text-align:center;font-family:"Roboto",sans-serif;font-weight:700;font-size:24px}

/* video */
.video{top:1369px;height:462px;background:linear-gradient(90deg,#3a3026 0%,#5b4a3d 35%,#4a3f37 60%,#2c2621 100%)}
.video h2{position:absolute;top:121px;width:100%;text-align:center;font-size:44px;color:var(--white);letter-spacing:.5px}
.video svg{position:absolute;left:551px;top:218px}

/* steps */
.steps{top:1831px;height:550px}
.steps h2{position:absolute;top:52px;width:100%;text-align:center;font-size:44px;color:var(--ink);letter-spacing:1px}
.step-line{position:absolute;top:308px;left:70px;width:1060px;height:2px;background:#f3a9ac}
.step{position:absolute;top:196px;width:260px;text-align:center}
.step svg{display:block;margin:0 auto}
.step .num{position:absolute;left:0;right:0;top:74px;font-size:110px;line-height:90px;color:var(--numeral)}
.step h3{position:relative;margin-top:38px;display:inline-block;padding:0 10px;background:var(--white);font-family:"Roboto",sans-serif;font-weight:700;font-size:25px;color:var(--ink)}
.step p{position:relative;margin:18px auto 0;width:240px;font-size:13px;line-height:20px;color:var(--text)}

/* partners */
.partners{top:2381px;height:325px;background:var(--red)}
.partners .title-line{position:absolute;top:87px;left:273px;width:662px;height:2px;background:rgba(255,255,255,.6)}
.partners h2{position:absolute;top:63px;left:345px;width:512px;height:50px;border:2px solid rgba(255,255,255,.85);background:var(--red);color:var(--white);font-size:36px;line-height:46px;text-align:center;letter-spacing:.5px}
.partner-row{position:absolute;top:154px;left:93px;display:flex;gap:22px}
.partner{width:153px;height:98px;background:var(--white);display:flex;align-items:center;justify-content:center;font-family:"Roboto",sans-serif;font-weight:700;font-size:21px;color:var(--ink)}

/* our work */
.work{top:2706px;height:545px;background:linear-gradient(160deg,#1a6cc0 0%,var(--blue) 45%,var(--blue-deep) 100%);overflow:hidden}
.work .panel-shape{position:absolute;left:73px;top:94px}
.work h2{position:absolute;top:104px;width:100%;text-align:center;font-size:40px;color:var(--ink)}
.book{position:absolute;top:195px;width:152px;height:228px;box-shadow:0 3px 8px rgba(0,0,0,.3)}
.book-1{left:148px;background:linear-gradient(180deg,#f4f0e8,#9fb45a 55%,#4d6e2f)}
.book-2{left:382px;background:linear-gradient(180deg,#2a2a2a,#0d0d0d)}
.book-3{left:652px;background:linear-gradient(180deg,#1c1c1c,#7a4a1c 50%,#d0932f)}
.book-4{left:901px;background:linear-gradient(180deg,#8f1a22,#6b1017)}
.arrow-btn{position:absolute;top:296px}

/* testimonials */
.testimonials{top:3251px;height:419px}
.testimonials h2{position:absolute;top:66px;left:93px;font-size:40px;color:var(--ink);letter-spacing:.5px}
.quote-box{position:absolute;top:136px;left:93px;width:717px;height:215px;background:var(--grey-box)}
.quote-photo{position:absolute;left:42px;top:43px;width:130px;height:130px;border-radius:50%;background:radial-gradient(circle at 50% 40%,#d2b49c,#8a6a55 70%,#5b4a3f)}
.quote-box p{position:absolute;left:206px;top:68px;width:470px;font-style:italic;font-size:21px;line-height:27px;color:var(--text)}
.quote-nav{position:absolute;top:95px;width:26px;height:26px;background:#3a3a3a}
.ad-space{position:absolute;top:78px;left:849px;width:275px;height:273px;background:var(--white);border:1px solid #ddd}
.ad-visual{position:absolute;left:0;top:0;width:132px;height:273px;background:linear-gradient(180deg,#6a2b20,#a13a2a 50%,#5a2418)}
.ad-copy{position:absolute;left:140px;top:30px;width:126px;text-align:center;color:#3a3a3a}
.ad-copy small{display:block;font-size:13px;letter-spacing:1px}
.ad-copy strong{display:block;font-size:21px;line-height:22px;font-weight:700;letter-spacing:.5px}
.ad-copy .ad-brand{margin-top:22px;font-size:16px;font-weight:700}
.ad-shop{position:absolute;left:152px;top:196px;width:104px;height:28px;background:#2a8ec9;color:var(--white);font-size:13px;font-weight:700;display:flex;align-items:center;justify-content:center}
.ad-url{position:absolute;left:140px;top:240px;width:126px;text-align:center;font-size:9px;color:#555}

/* footer */
.site-footer{top:3670px;height:226px;background:var(--navy);color:var(--white)}
.footer-brand{position:absolute;left:213px;top:13px;width:135px;height:135px;border-radius:50%;background:var(--white);display:flex;align-items:center;justify-content:center;text-align:center;font-weight:700;font-size:17px;line-height:1.15;color:var(--navy)}
.footer-col{position:absolute;top:52px;list-style:none;font-size:15px;line-height:26px}
.social-title{position:absolute;left:789px;top:52px;font-size:13px;font-weight:700;letter-spacing:.3px}
.social{position:absolute;left:789px;top:85px;display:flex;gap:4px}
.social span{width:36px;height:36px}
.footer-rule{position:absolute;left:213px;top:173px;width:774px;height:1px;background:rgba(255,255,255,.25)}
.copyright{position:absolute;top:192px;width:100%;text-align:center;font-size:13px;color:rgba(255,255,255,.85)}
</style>
</head>
<body>

<section class="hero">
  <div class="hero-photo" role="img" aria-label="Photo of a smiling woman writing on a laptop"></div>
  <header class="topbar">
    <div class="brand">Velmora<br>Publishing</div>
    <ul class="menu">
      <li>HOME</li><li>PUBLISHING</li><li>SUBMISSIONS</li><li>BOOKS</li><li>AUTHORS</li><li>SEMINARS</li><li>CONTACT</li>
    </ul>
    <div class="menu-tools">
      <svg width="24" height="24" viewBox="0 0 24 24" fill="none" stroke="#fff" stroke-width="2.4"><circle cx="10" cy="10" r="7"/><line x1="15" y1="15" x2="22" y2="22"/></svg>
      <svg width="24" height="24" viewBox="0 0 24 24" fill="none" stroke="#fff" stroke-width="2.2"><path d="M4 7h16l-1.5 14h-13z"/><path d="M8 9V5a4 4 0 0 1 8 0v4"/></svg>
    </div>
  </header>
  <div class="hero-title">
    <h1 class="head">VELMORA PUBLISHING</h1>
    <p class="head">SELF-PUBLISHING THAT WORKS</p>
  </div>
  <div class="btn-red">SUBMIT BOOK</div>
  <div class="dots"><span class="on"></span><span></span><span></span><span></span><span></span></div>
</section>

<section class="intro">
  <h2>Have a story to tell? We can help you publish your book.</h2>
  <div class="rule"></div>
  <p>Welcome to Velmora Publishing, we are an independent publishing company located in London/Surrey. We publish Trade (fiction and non-fiction), &amp; Young Adult (YA) in a variety of subjects.</p>
</section>

<section class="categories">
  <svg width="1200" height="110" viewBox="0 0 1200 110" style="position:absolute;top:0;left:0"><polygon points="0,0 1200,0 1200,20 600,105 0,20" fill="#fff"/></svg>
  <div class="tile tile-books">
    <svg width="84" height="76" viewBox="0 0 84 76" fill="none" stroke="#fff" stroke-width="4"><rect x="6" y="6" width="66" height="16" rx="3"/><rect x="12" y="30" width="66" height="16" rx="3"/><rect x="4" y="54" width="70" height="16" rx="3"/></svg>
    <span>BOOKS</span>
  </div>
  <div class="tile tile-authors">
    <svg width="76" height="80" viewBox="0 0 76 80" fill="#fff"><circle cx="38" cy="22" r="18"/><path d="M4 80c0-22 14-34 34-34s34 12 34 34z"/></svg>
    <span>AUTHORS</span>
  </div>
  <div class="tile tile-submissions">
    <svg width="84" height="76" viewBox="0 0 84 76" fill="none" stroke="#fff" stroke-width="5"><path d="M50 14H8v56h56V50"/><path d="M30 50c4-18 18-26 36-26" /><path d="M58 10l16 14-16 14" fill="#fff"/></svg>
    <span>SUBMISSIONS</span>
  </div>
</section>

<section class="video" role="img" aria-label="Video still of two women talking in a bookshop">
  <h2 class="head">LEARN HOW WE PUBLISH BOOKS</h2>
  <svg width="98" height="98" viewBox="0 0 98 98"><circle cx="49" cy="49" r="45" fill="none" stroke="#fff" stroke-width="6"/><polygon points="39,29 69,49 39,69" fill="#fff"/></svg>
</section>

<section class="steps">
  <h2 class="head">PUBLISH YOUR BOOK IN 4 EASY STEPS</h2>
  <div class="step-line"></div>
  <div class="step" style="left:65px">
    <svg width="60" height="60" viewBox="0 0 60 60" fill="none" stroke="#0255a3" stroke-width="2.5"><path d="M12 48l4-14 30-30 10 10-30 30z"/><path d="M40 10l10 10"/><path d="M12 48l14-4"/></svg>
    <div class="num head">1.</div>
    <h3>WRITING</h3>
    <p>You write a book to the best of your ability And after redrafting several times when you honestly feel that you have done the best you Possibly can with it, you send it to us</p>
  </div>
  <div class="step" style="left:337px">
    <svg width="60" height="60" viewBox="0 0 60 60" fill="none" stroke="#0255a3" stroke-width="2.5"><path d="M14 4h22l12 12v40H14z"/><path d="M36 4v12h12"/><path d="M31 46V26M23 34l8-8 8 8"/></svg>
    <div class="num head">2.</div>
    <h3>SUBMISSION</h3>
    <p>If your book is in our subject matter and you think you have something that could tickle our fancy, send Us your book for review.</p>
  </div>
  <div class="step" style="left:605px">
    <svg width="60" height="60" viewBox="0 0 60 60" fill="none" stroke="#0255a3" stroke-width="2.5"><polygon points="30,6 37,22 54,22 40,33 45,50 30,40 15,50 20,33 6,22 23,22"/><path d="M14 56h32"/></svg>
    <div class="num head">3.</div>
    <h3>REVIEW</h3>
    <p>You send us your book and our editorial team will look over it and decide if we like it and</p>
  </div>
  <div class="step" style="left:875px">
    <svg width="60" height="60" viewBox="0 0 60 60" fill="none" stroke="#0255a3" stroke-width="2.5"><rect x="12" y="8" width="36" height="48" rx="2"/><rect x="22" y="4" width="16" height="8"/><path d="M19 24l3 3 5-6M31 24h11M19 36l3 3 5-6M31 36h11M19 47h23"/></svg>
    <div class="num head">4.</div>
    <h3>CONTRACT</h3>
    <p>You send us your book and our editorial team will look over it and decide if we like it and then we will Decide what</p>
  </div>
</section>

<section class="partners">
  <div class="title-line"></div>
  <h2 class="head">COMPANIES WE WORK WITH</h2>
  <div class="partner-row">
    <div class="partner">Riverleaf</div>
    <div class="partner">Quillon</div>
    <div class="partner">Tallowreed</div>
    <div class="partner">Brightfold</div>
    <div class="partner">Hart &amp; Vale</div>
    <div class="partner">Marginly</div>
  </div>
</section>

<section class="work">
  <svg class="panel-shape" width="1054" height="386" viewBox="0 0 1054 386"><path d="M6 28h340l16-24h330l16 24h340v352H6z" fill="#f6f6f6" stroke="#dcdcdc" stroke-width="2"/></svg>
  <h2 class="head">OUR WORK</h2>
  <div class="book book-1" role="img" aria-label="Book cover: lifestyle title with photo collage"></div>
  <div class="book book-2" role="img" aria-label="Book cover: black cover with white title"></div>
  <div class="book book-3" role="img" aria-label="Book cover: illustrated desert scene"></div>
  <div class="book book-4" role="img" aria-label="Book cover: deep red cloth cover"></div>
  <svg class="arrow-btn" style="left:62px" width="32" height="32" viewBox="0 0 32 32"><circle cx="16" cy="16" r="14" fill="#fff" stroke="#555" stroke-width="2"/><path d="M19 9l-7 7 7 7" fill="none" stroke="#555" stroke-width="2.5"/></svg>
  <svg class="arrow-btn" style="left:1106px" width="32" height="32" viewBox="0 0 32 32"><circle cx="16" cy="16" r="14" fill="#fff" stroke="#555" stroke-width="2"/><path d="M13 9l7 7-7 7" fill="none" stroke="#555" stroke-width="2.5"/></svg>
</section>

<section class="testimonials">
  <h2 class="head">TESTIMONIALS</h2>
  <div class="quote-box">
    <div class="quote-nav" style="left:0"><svg width="26" height="26" viewBox="0 0 26 26"><path d="M16 7l-6 6 6 6" fill="none" stroke="#fff" stroke-width="2.5"/></svg></div>
    <div class="quote-photo" role="img" aria-label="Portrait of the reviewing author"></div>
    <p>"You send us your book and our editorial team will look over it and decide if we like it and then we will Decide what."</p>
    <div class="quote-nav" style="left:691px"><svg width="26" height="26" viewBox="0 0 26 26"><path d="M10 7l6 6-6 6" fill="none" stroke="#fff" stroke-width="2.5"/></svg></div>
  </div>
  <aside class="ad-space">
    <div class="ad-visual" role="img" aria-label="Advert photo of a red wooden wristwatch"></div>
    <div class="ad-copy">
      <small>LUXURY</small>
      <strong>WOOD<br>WATCHES</strong>
      <div class="ad-brand">Timberline</div>
    </div>
    <div class="ad-shop">SHOP NOW</div>
    <div class="ad-url">TIMBERLINEWATCHES.COM</div>
  </aside>
</section>

<footer class="site-footer">
  <div class="footer-brand">Velmora<br>Publishing</div>
  <ul class="footer-col" style="left:392px"><li>Submissions</li><li>Production</li><li>Ebooks</li></ul>
  <ul class="footer-col" style="left:548px"><li>Books</li><li>Seminars</li><li>Packages</li></ul>
  <ul class="footer-col" style="left:675px"><li>Authors</li><li>Contact</li><li>Career</li></ul>
  <div class="social-title">STAY CONNECTED</div>
  <div class="social" aria-label="Social media links">
    <span style="background:#3b5998"></span><span style="background:#1da1f2"></span><span style="background:#d34836"></span><span style="background:#0077b5"></span><span style="background:#cb2027"></span>
  </div>
  <div class="footer-rule"></div>
  <div class="copyright">© 2016 Velmora Publishing. All Rights Reserved.</div>
</footer>

</body>
</html>
```